Redesign Canvas Art E-Commerce Website

Help! I hired a couple of companies on Brisklo.com to build and design an e-commerce website for me. After three long and painful months, I have one that I believe is functional on the back-end, but aesthetically on the front end is a mess.

We are a small family business that will take your digital photo and manipulate it into a digitally created oil, watercolor or impressionist style pieces of artwork that we print on museum quality, gallery grade canvas and ship to the customer, ready to hang.

We are looking to create an e-commerce website where a customer can choose their art style, upload a photo, choose their canvas size and orientation (horizontal or vertical) and checkout. Within 48 hours, we will send them back a proof of their newly created, customized artwork for them to approve or not approve. If they approve, we print, package and ship them the product. If they do not approve, we offer unlimited revisions until they are happy.

As I mentioned, the back end functionality is already there, just need design help. No coding required

Here is a link to the development page that they created: https://plumwickstudio.com/development/

As you can see, it looks off...doesnt line up properly, wasted space, weird font. Feel free to either correct the homepage they created or design an entirely new page. I am attaching some examples of before and after photos of artwork for reference. I also think the testimonials page and shop page can use a little style. The content is there and accurate, it just doesn't look pretty. Please keep in mind that our customers will probably not be very tech savvy. The customers will probably be sending us pics of kids, grandkids, pets, family portraits, vacation photos, etc.

Here is one of our competitors - www.gildavantry.com
Their website looks clean and inviting.

Thank you in advance! Im looking forward to seeing the results. I am including our logo in the attachments (I do not have it in a vector file, just a jpeg)

Target Market(s)

Non tech-savvy indiduals, 30-70 years old

Industry/Entity Type

Please look at https://plumwickstudio.com/development/ to see various pages and what the other designers did

Number of Pages Required

1 page

Requirements
Must have
• Verbiage on pages leave "as is" but feel free to change styles. Would like to keep existing four categories on homepage
Nice to have
• Warm and inviting homepage that evokes emotion

```html
<!DOCTYPE html>
<html lang="en">
<head>
<meta charset="utf-8">
<title>Brushfield Prints – Turn Your Digital Photos Into Wall Art</title>
<link href="https://fonts.googleapis.com/css2?family=Kanit:wght@300;600&family=Roboto:wght@400;500;700&display=swap" rel="stylesheet">
<style>
:root{
  --teal:#2fb0d0;
  --teal-text:#29a9cc;
  --ink:#111;
  --body:#555;
  --hero-bg:#e7f7fb;
  --cat-bg:#fdf4ee;
  --orange:#e45a1c;
  --grad-a:#e8401a;
  --grad-b:#f2b81f;
  --footer:#333;
  --white:#fff;
}
*{box-sizing:border-box;margin:0;padding:0}
html,body{width:1200px;height:3536px;overflow:hidden}
body{font-family:'Roboto',sans-serif;color:var(--body);background:var(--white);position:relative}
.abs{position:absolute}
.heading{font-family:'Kanit',sans-serif;font-weight:600;color:var(--ink);text-transform:uppercase}
.heading .light{font-weight:300;color:var(--teal-text)}
.btn{position:absolute;display:flex;align-items:center;justify-content:center;color:var(--white);font-weight:700;font-size:15px;text-transform:uppercase;border-radius:6px;background:linear-gradient(90deg,var(--grad-a),var(--grad-b))}
.brand{display:flex;align-items:center;gap:10px;font-family:'Roboto',sans-serif;font-weight:700;font-size:24px;color:var(--ink)}
.brand .dot{width:30px;height:30px;border-radius:50%;background:var(--orange)}

/* header */
.header{top:0;left:0;width:1200px;height:120px}
.header .brand{left:111px;top:40px}
.socials{left:738px;top:42px;display:flex;gap:10px}
.socials span{width:36px;height:36px;border-radius:50%;background:var(--teal)}
.cart{left:945px;top:38px;width:44px;height:44px;background:var(--white);box-shadow:0 2px 10px rgba(0,0,0,.12);border-radius:4px;display:flex;align-items:center;justify-content:center}
.cart-label{left:1012px;top:42px;font-size:11px;color:#555;text-transform:uppercase}
.cart-total{left:1012px;top:56px;font-size:20px;font-weight:700;color:var(--ink)}
.nav{top:120px;left:0;width:1200px;height:52px;background:var(--teal);display:flex;justify-content:center;align-items:center;gap:40px}
.nav a{color:var(--white);font-size:14px;font-weight:700;text-decoration:none;text-transform:uppercase}

/* hero */
.hero{top:172px;left:0;width:1200px;height:600px;background:var(--hero-bg)}
.hero h1{left:111px;top:140px;font-size:40px;line-height:52px;width:560px}
.hero p{left:111px;top:310px;width:500px;font-size:18px;line-height:30px;color:#444}
.hero .btn{left:111px;top:400px;width:149px;height:49px}
.hero-splash{left:650px;top:90px;width:535px;height:420px;border-radius:50%;background:radial-gradient(circle,rgba(230,60,60,.25),rgba(47,176,208,.15) 55%,transparent 72%)}
.hero-frame{left:780px;top:130px;width:276px;height:340px;background:var(--white);border-radius:12px;padding:6px;box-shadow:0 6px 20px rgba(0,0,0,.15)}
.ph{width:100%;height:100%}

/* about */
.about{top:772px;left:0;width:1200px;height:654px}
.pic{position:absolute;background:var(--white);padding:8px}
.about h2{left:700px;top:155px;font-size:40px}
.about p{left:700px;top:228px;width:389px;font-size:14px;line-height:26.7px;text-align:justify}
.about .btn{left:700px;top:451px;width:141px;height:49px}

/* categories */
.categories{top:1426px;left:0;width:1200px;height:1106px;background:var(--cat-bg)}
.categories h2{left:0;width:1200px;text-align:center;top:80px;font-size:40px}
.cat-card{position:absolute;width:460px;height:403px;background:var(--white);box-shadow:0 4px 16px rgba(0,0,0,.08);padding:7px}
.cat-card .ph{height:312px}
.cat-card h3{text-align:center;margin-top:30px;color:var(--orange);font-size:20px;font-weight:700;text-transform:uppercase}

/* why us */
.why{top:2532px;left:0;width:1200px;height:658px}
.why h2{left:0;width:1200px;text-align:center;top:100px;font-size:40px}
.why-card{position:absolute;top:190px;width:306px;height:353px;background:var(--white);box-shadow:0 4px 18px rgba(47,176,208,.18);text-align:center;padding:38px 30px 0}
.why-card .icon{width:90px;height:90px;border-radius:50%;margin:0 auto;background:linear-gradient(135deg,var(--grad-a),var(--grad-b));display:flex;align-items:center;justify-content:center}
.why-card h3{margin-top:34px;color:var(--teal-text);font-size:17px;font-weight:500;text-transform:uppercase}
.why-card p{margin-top:12px;font-size:14px;line-height:26px;color:#666}

/* footer */
.footer{top:3190px;left:0;width:1200px;height:346px;background:var(--footer);color:var(--white)}
.footer .brand{left:111px;top:48px;color:var(--white)}
.flinks{font-size:15px;line-height:35px}
.flinks a{display:block;color:var(--white);text-decoration:none}
.footer h4{left:596px;top:88px;font-size:20px;font-weight:500;text-transform:uppercase}
.email-input{left:596px;top:130px;width:300px;height:48px;border-bottom:1px solid #888;font-size:14px;padding-top:18px}
.footer .btn{left:933px;top:132px;width:135px;height:50px}
.contact-row{left:596px;top:210px;font-size:15px;display:flex;align-items:center;gap:14px}
.contact-row .mini{width:12px;height:12px;border-radius:50%;background:var(--white);display:inline-block}
.rule{left:111px;top:285px;width:979px;height:1px;background:#555}
.copy{left:111px;top:306px;font-size:12px}
.cards{left:838px;top:300px;display:flex;gap:4px}
.cards span{width:46px;height:26px;border-radius:3px;background:#e8e8e8}
</style>
</head>
<body>

<header class="abs header">
  <div class="abs brand"><span class="dot"></span>Brushfield Prints</div>
  <div class="abs socials" aria-label="Social links"><span></span><span></span><span></span><span></span></div>
  <div class="abs cart"><svg width="18" height="16" viewBox="0 0 18 16"><path d="M1 1h3l2 9h9l2-7H5" fill="none" stroke="#e8401a" stroke-width="2"/><circle cx="7" cy="14" r="1.5" fill="#e8401a"/><circle cx="14" cy="14" r="1.5" fill="#e8401a"/></svg></div>
  <div class="abs cart-label">Add to cart:</div>
  <div class="abs cart-total">0.00</div>
</header>
<nav class="abs nav">
  <a href="#">Home</a><a href="#">Shop</a><a href="#">Testimonials</a><a href="#">About Us</a><a href="#">FAQs</a><a href="#">My Orders</a><a href="#">Contact Us</a>
</nav>

<section class="abs hero">
  <h1 class="abs heading">Turn your digital photos into <span class="light">one of a kind wall art</span></h1>
  <p class="abs">At Brushfield Prints, we take your digital photo and turn it into a one-of-a-kind piece of artwork!</p>
  <a class="btn" style="font-size:14px">Get Started</a>
  <div class="abs hero-splash"></div>
  <div class="abs hero-frame"><div class="ph" role="img" aria-label="Painted portrait of a bride holding a bouquet" style="background:linear-gradient(160deg,#6b4a34,#c9a184 45%,#e9e2c8 75%,#8a7a5a);border-radius:8px"></div></div>
</section>

<section class="abs about">
  <div class="pic" style="left:306px;top:116px;width:339px;height:250px;padding:8px;background:transparent"><div class="ph" role="img" aria-label="Painted puppy portrait" style="background:linear-gradient(135deg,#8b7b6a,#d8d2cc 50%,#7a8fa0)"></div></div>
  <div class="pic" style="left:114px;top:235px;width:304px;height:212px"><div class="ph" role="img" aria-label="Painted show-jumping horse and rider" style="background:linear-gradient(120deg,#9cc8e6,#7a3a1c 50%,#b8d6ee)"></div></div>
  <div class="pic" style="left:306px;top:330px;width:282px;height:219px"><div class="ph" role="img" aria-label="Painted happy older couple outdoors" style="background:linear-gradient(135deg,#5f7f4a,#c8c2b0 50%,#6a8a5c)"></div></div>
  <h2 class="abs heading">About <span class="light">Us</span></h2>
  <p class="abs">At Brushfield Prints, we take your digital photo and turn it into a one-of-a-kind piece of artwork! The process couldn't be any easier. Simply upload your photo, choose your art style and size, and let our team of skilled digital artists do the rest. Do you want to put your digital photo on canvas without an art style? No problem! Just choose the “Digital Photo/Retouching” category and upload your photo.</p>
  <a class="btn">Learn More</a>
</section>

<section class="abs categories">
  <h2 class="abs heading">Our <span class="light">Categories</span></h2>
  <div class="cat-card" style="left:125px;top:171px"><div class="ph" role="img" aria-label="Oil painting style wedding couple" style="background:linear-gradient(135deg,#2f4a22,#7a3a22 40%,#d8d0c0 60%,#2a3a1c)"></div><h3>Oil</h3></div>
  <div class="cat-card" style="left:615px;top:171px"><div class="ph" role="img" aria-label="Watercolor style mother and baby" style="background:linear-gradient(135deg,#f3ece6,#e9c2a8 50%,#f7f2ee)"></div><h3>Watercolor</h3></div>
  <div class="cat-card" style="left:125px;top:614px"><div class="ph" role="img" aria-label="Impressionist style dog with cat" style="background:linear-gradient(135deg,#a05022,#3a2416 45%,#d88a3a 70%,#c8c4c0)"></div><h3>Impressionist</h3></div>
  <div class="cat-card" style="left:615px;top:614px"><div class="ph" role="img" aria-label="Photo of parent and child walking on a path" style="background:linear-gradient(135deg,#3a5a2a,#a8a49a 50%,#5a6a8a)"></div><h3>Digital Photo</h3></div>
</section>

<section class="abs why">
  <h2 class="abs heading">Why <span class="light">Us?</span></h2>
  <div class="why-card" style="left:111px"><div class="icon"><svg width="44" height="44" viewBox="0 0 44 44" fill="none" stroke="#fff" stroke-width="2"><path d="M8 36L30 14l4 4-22 22H8z"/><circle cx="14" cy="14" r="6"/><circle cx="32" cy="32" r="5"/></svg></div><h3>Your Idea Your Design</h3><p>Each art piece is customized for you! You choose your size, orientation and art style. Makes a perfect gift!!!</p></div>
  <div class="why-card" style="left:448px"><div class="icon"><svg width="48" height="40" viewBox="0 0 48 40" fill="none" stroke="#fff" stroke-width="2"><rect x="6" y="8" width="24" height="20"/><path d="M30 14h8l6 7v7H30"/><circle cx="14" cy="31" r="4"/><circle cx="36" cy="31" r="4"/><path d="M12 18l4 4 7-7"/></svg></div><h3>Fast Shipping</h3><p>Your artwork is printed and shipped in the USA! We offer fast turnaround with transit times typically 3-7 days. Free tracking with each order!!</p></div>
  <div class="why-card" style="left:783px"><div class="icon"><svg width="44" height="40" viewBox="0 0 44 40" fill="none" stroke="#fff" stroke-width="2"><path d="M6 14l8-8h16l8 8-16 20z"/><path d="M6 14h32M16 6l6 28 6-28"/></svg></div><h3>High Quality</h3><p>We've put a lot of effort ensuring your artwork is of the highest quality. Each piece is printed on the highest quality, gallery grade canvas. It is ready to hang upon arrival.!</p></div>
</section>

<footer class="abs footer">
  <div class="abs brand"><span class="dot"></span>Brushfield Prints</div>
  <div class="abs flinks" style="left:111px;top:134px"><a>Home</a><a>Shop</a><a>Testimonials</a><a>About Us</a></div>
  <div class="abs flinks" style="left:334px;top:134px"><a>FAQs</a><a>My Orders</a><a>Contact Us</a></div>
  <h4 class="abs">Join our newsletter</h4>
  <div class="abs email-input">Enter Your Email Here</div>
  <a class="btn">Subscribe</a>
  <div class="abs contact-row"><svg width="14" height="11" viewBox="0 0 14 11"><rect width="14" height="11" fill="#fff"/><path d="M0 0l7 6 7-6" stroke="#333" fill="none"/></svg>info@brushfieldprints.com<span style="margin:0 14px">|</span><span class="mini"></span><span class="mini"></span><span class="mini"></span><span class="mini"></span></div>
  <div class="abs rule"></div>
  <div class="abs copy">© 2023 Brushfield Prints &nbsp;|&nbsp; All Rights Reserved</div>
  <div class="abs cards" aria-label="Accepted payment methods"><span></span><span></span><span></span><span></span><span></span></div>
</footer>

</body>
</html>
```